For Sale Sign for Real Estate Agency

We need a For Sale Sign designed for our agency. I want a very simple/elegant sign that says "For Sale" towards the top of the sign (not in huge letters). Most of the sign should be a design/picture with our name and phone number somewhere at the bottom.

One significant detail, it's important that our logo not be too big or the center piece of the sign. Since our company name has the word "rent" in it, people assume the house is for rent, instead of for sale.

I attached our logo and a rough outline of the format I'm looking for.

Again, I'm looking for elegant and simple! Thanks for your time

Industry/Entity Type

Real Estate

Colors

Designer to choose colors to be used in the design.

Requirements
Must have
Nice to have
Should not have
• Nothing tacky!
• Our logo/company name should not be too big or the center piece of the sign. Since our company name has the word "rent" in it, people assume the house is for rent, instead of for sale.

```html
<!DOCTYPE html>
<html lang="en">
<head>
<meta charset="utf-8">
<title>For Sale Signs – HearthKey Realty</title>
<link href="https://fonts.googleapis.com/css2?family=Libre+Baskerville:ital,wght@0,400;0,700;1,400&family=Playfair+Display:ital,wght@1,500&display=swap" rel="stylesheet">
<style>
  :root {
    --backdrop: #e3e3e3;
    --sky-top: #5d8fd2;
    --sky-low: #b9cfe6;
    --house: #b7aa90;
    --house-trim: #cfc7b4;
    --drive: #9d9d98;
    --lawn: #74ad3e;
    --sign-red: #c9211c;
    --sign-red-deep: #ab1410;
    --band-black: #161616;
    --white: #ffffff;
    --gold: #f5c65a;
    --shadow-ink: #1f2430;
  }
  * { margin: 0; padding: 0; box-sizing: border-box; }
  html, body { width: 837px; height: 1200px; overflow: hidden; background: var(--backdrop); }
  .board {
    position: relative;
    width: 837px;
    height: 1200px;
    font-family: "Libre Baskerville", Georgia, serif;
  }

  /* shared sign parts */
  .sign {
    position: absolute;
    overflow: hidden;
    background: var(--sign-red);
    box-shadow: 2px 3px 6px rgba(0,0,0,0.35);
  }
  .property-photo {
    position: absolute;
    left: 0; top: 0; width: 100%;
    background: linear-gradient(180deg,
      var(--sky-top) 0%,
      var(--sky-low) 40%,
      var(--house-trim) 46%,
      var(--house) 56%,
      var(--house) 74%,
      var(--drive) 84%,
      var(--lawn) 92%,
      var(--lawn) 100%);
  }
  .band { position: absolute; left: 0; top: 0; }
  .headline { position: absolute; left: 0; width: 100%; text-align: center; font-weight: 400; }
  .headline-for {
    font-family: "Playfair Display", Georgia, serif;
    font-style: italic;
    font-weight: 500;
    color: var(--gold);
  }
  .headline-sale {
    font-weight: 700;
    color: var(--white);
    letter-spacing: -1px;
    text-shadow: 2px 2px 0 var(--shadow-ink);
  }
  .phone-icon { position: absolute; }
  .contact-box {
    position: absolute;
    border: 1px solid rgba(255,255,255,0.8);
    border-radius: 7px;
    text-align: center;
    color: var(--white);
  }
  .phone-number { font-weight: 400; line-height: 1.1; white-space: nowrap; }
  .website { font-style: italic; white-space: nowrap; }
  .agency-name { position: absolute; color: var(--white); line-height: 1; }
  .name-main { display: block; letter-spacing: -0.5px; }
  .name-sub { display: block; text-align: right; }
  .office-details { position: absolute; list-style: none; color: var(--white); line-height: 1.2; }
  .office-details li { position: relative; }
  .office-details svg { position: absolute; left: 0; }

  /* landscape sign */
  .sign--landscape { left: 122px; top: 56px; width: 596px; height: 420px; }
  .sign--landscape .property-photo { height: 330px; }
  .sign--landscape .headline { top: 8px; line-height: 1; }
  .sign--landscape .headline-for { font-size: 46px; margin-right: 6px; }
  .sign--landscape .headline-sale { font-size: 62px; }
  .sign--landscape .phone-icon { left: 286px; top: 310px; width: 20px; height: 20px; }
  .sign--landscape .contact-box { left: 193px; top: 322px; width: 210px; height: 60px; padding-top: 9px; }
  .sign--landscape .phone-number { font-size: 26px; }
  .sign--landscape .website { font-size: 8px; letter-spacing: 4px; margin-top: 3px; }
  .sign--landscape .agency-name { left: 10px; top: 366px; }
  .sign--landscape .name-main { font-size: 21px; }
  .sign--landscape .name-sub { font-size: 11px; letter-spacing: 3px; margin-top: 2px; }
  .sign--landscape .office-details { left: 428px; top: 373px; font-size: 8.5px; }
  .sign--landscape .office-details li { padding-left: 18px; margin-bottom: 4px; }
  .sign--landscape .office-details svg { width: 9px; height: 9px; top: 0; }

  /* portrait sign */
  .sign--portrait { left: 185px; top: 516px; width: 471px; height: 654px; }
  .sign--portrait .property-photo { height: 500px; }
  .sign--portrait .headline { top: 0; }
  .sign--portrait .headline-for { display: block; font-size: 64px; line-height: 1.1; }
  .sign--portrait .headline-sale { display: block; font-size: 84px; line-height: 1.05; }
  .sign--portrait .phone-icon { left: 224px; top: 495px; width: 22px; height: 22px; }
  .sign--portrait .contact-box { left: 113px; top: 508px; width: 245px; height: 70px; padding-top: 11px; }
  .sign--portrait .phone-number { font-size: 30px; }
  .sign--portrait .website { font-size: 9px; letter-spacing: 5px; margin-top: 4px; }
  .sign--portrait .agency-name { left: 13px; top: 604px; }
  .sign--portrait .name-main { font-size: 22px; }
  .sign--portrait .name-sub { font-size: 11.5px; letter-spacing: 3px; margin-top: 2px; }
  .sign--portrait .office-details { left: 290px; top: 604px; font-size: 10px; }
  .sign--portrait .office-details li { padding-left: 14px; margin-bottom: 4px; }
  .sign--portrait .office-details svg { width: 8px; height: 8px; top: 2px; }
</style>
</head>
<body>
<main class="board">

  <section class="sign sign--landscape" aria-label="Landscape for sale sign">
    <div class="property-photo" role="img" aria-label="Photograph of a two-storey suburban house with garage, porch, hedge and green lawn under a blue sky"></div>
    <svg class="band" width="596" height="420" viewBox="0 0 596 420" aria-hidden="true">
      <defs>
        <linearGradient id="redFillWide" x1="0" y1="0" x2="1" y2="1">
          <stop offset="0" stop-color="var(--sign-red)"/>
          <stop offset="1" stop-color="var(--sign-red-deep)"/>
        </linearGradient>
      </defs>
      <path d="M0 256 C 120 244 230 250 310 268 C 410 290 500 304 596 300 L596 420 L0 420 Z" fill="var(--band-black)"/>
      <path d="M0 266 C 130 262 240 275 330 295 C 430 316 520 322 596 320 L596 420 L0 420 Z" fill="url(#redFillWide)"/>
      <path d="M0 272 C 140 250 300 262 596 342" fill="none" stroke="var(--white)" stroke-width="1.5"/>
      <path d="M0 312 C 160 306 360 256 596 262" fill="none" stroke="var(--white)" stroke-width="1.5"/>
    </svg>
    <h1 class="headline"><span class="headline-for">For</span><span class="headline-sale">SALE</span></h1>
    <svg class="phone-icon" viewBox="0 0 40 40" aria-hidden="true">
      <circle cx="20" cy="20" r="17" fill="var(--sign-red)" stroke="var(--white)" stroke-width="3"/>
      <path d="M14 12 l4 0 l1.5 5 l-2.5 1.8 a11 11 0 0 0 5 5 l1.8 -2.5 l5 1.5 l0 4 a2 2 0 0 1 -2 2 A16 16 0 0 1 12 14 a2 2 0 0 1 2 -2 Z" fill="var(--white)"/>
    </svg>
    <div class="contact-box">
      <p class="phone-number">(555) 318-4470</p>
      <p class="website">www.hearthkeyrealty.com</p>
    </div>
    <p class="agency-name"><span class="name-main">HearthKey</span><span class="name-sub">Realty</span></p>
    <ul class="office-details">
      <li><svg viewBox="0 0 14 14" aria-hidden="true"><rect x="1" y="3" width="12" height="8" fill="var(--white)"/><path d="M1 3 L7 8 L13 3" fill="none" stroke="var(--sign-red)" stroke-width="1.2"/></svg>hello@hearthkeyrealty.com</li>
      <li><svg viewBox="0 0 14 14" aria-hidden="true"><path d="M7 13 C 3 8 2 6.5 2 5 a5 5 0 0 1 10 0 c0 1.5 -1 3 -5 8 Z" fill="var(--white)"/><circle cx="7" cy="5" r="1.8" fill="var(--sign-red)"/></svg>142 Orchard Lane Westbrook,<br>RI 02900</li>
    </ul>
  </section>

  <section class="sign sign--portrait" aria-label="Portrait for sale sign">
    <div class="property-photo" role="img" aria-label="Photograph of a two-storey suburban house with garage, porch, driveway and green lawn under a blue sky"></div>
    <svg class="band" width="471" height="654" viewBox="0 0 471 654" aria-hidden="true">
      <defs>
        <linearGradient id="redFillTall" x1="0" y1="0" x2="1" y2="1">
          <stop offset="0" stop-color="var(--sign-red)"/>
          <stop offset="1" stop-color="var(--sign-red-deep)"/>
        </linearGradient>
      </defs>
      <path d="M0 424 C 110 410 240 410 320 430 C 390 448 435 456 471 452 L471 654 L0 654 Z" fill="var(--band-black)"/>
      <path d="M0 436 C 140 430 260 440 340 458 C 400 470 440 478 471 477 L471 654 L0 654 Z" fill="url(#redFillTall)"/>
      <path d="M0 446 C 150 420 300 440 471 494" fill="none" stroke="var(--white)" stroke-width="1.5"/>
      <path d="M0 490 C 160 486 320 440 471 436" fill="none" stroke="var(--white)" stroke-width="1.5"/>
    </svg>
    <h1 class="headline"><span class="headline-for">For</span><span class="headline-sale">SALE</span></h1>
    <svg class="phone-icon" viewBox="0 0 40 40" aria-hidden="true">
      <circle cx="20" cy="20" r="17" fill="var(--sign-red)" stroke="var(--white)" stroke-width="3"/>
      <path d="M14 12 l4 0 l1.5 5 l-2.5 1.8 a11 11 0 0 0 5 5 l1.8 -2.5 l5 1.5 l0 4 a2 2 0 0 1 -2 2 A16 16 0 0 1 12 14 a2 2 0 0 1 2 -2 Z" fill="var(--white)"/>
    </svg>
    <div class="contact-box">
      <p class="phone-number">(555) 318-4470</p>
      <p class="website">www.hearthkeyrealty.com</p>
    </div>
    <p class="agency-name"><span class="name-main">HearthKey</span><span class="name-sub">Realty</span></p>
    <ul class="office-details">
      <li><svg viewBox="0 0 14 14" aria-hidden="true"><rect x="1" y="3" width="12" height="8" fill="var(--white)"/><path d="M1 3 L7 8 L13 3" fill="none" stroke="var(--sign-red)" stroke-width="1.2"/></svg>hello@hearthkeyrealty.com</li>
      <li><svg viewBox="0 0 14 14" aria-hidden="true"><path d="M7 13 C 3 8 2 6.5 2 5 a5 5 0 0 1 10 0 c0 1.5 -1 3 -5 8 Z" fill="var(--white)"/><circle cx="7" cy="5" r="1.8" fill="var(--sign-red)"/></svg>142 Orchard Lane Westbrook,<br>RI 02900</li>
    </ul>
  </section>

</main>
</body>
</html>
```